Sales sheet for printing and embroidery apparel items - Copper Hollow Graphics

I would like a one page flyer or sales sheet that I would use as a template to send different images of apparel we produce. I have attached examples of layouts I like.
- Ideally, it would have space for 3-5 items.
- I would like it one page only - not a folding flyer.
- Our companies name is Copper Hollow Graphics.
- This will be used for many different products and markets so I don't need wording/copy. You can use wording from the 7M9 or T58 flyer.

Colors
0054AA
0677BA
7BADD7
CADEEF
E8F1F8
00AB8E
00BBA5
67D7C9
C6EFE9
E9F9F6
FFC000
F8CF3A
FAE287
FDF2CF
FEFAEE

Requirements
Must have
• Places for between 3 and 5 images of apparel (t-shirts, hats etc)

```html
<!DOCTYPE html>
<html lang="en">
<head>
<meta charset="utf-8">
<title>Copper Hollow Graphics – Sales Sheet</title>
<link href="https://fonts.googleapis.com/css2?family=Barlow+Condensed:ital,wght@0,400;0,500;0,700;0,800;1,400;1,500;1,700;1,800&display=swap" rel="stylesheet">
<style>
:root{
  --blue-deep:#0054AA;
  --blue:#0677BA;
  --blue-soft:#7BADD7;
  --blue-pale:#CADEEF;
  --blue-mist:#E8F1F8;
  --teal:#00AB8E;
  --teal-bright:#00BBA5;
  --teal-soft:#67D7C9;
  --teal-pale:#C6EFE9;
  --gold:#FFC000;
  --gold-soft:#F8CF3A;
  --gold-pale:#FAE287;
  --white:#ffffff;
  --stage:#d9d9d9;
}
*{margin:0;padding:0;box-sizing:border-box}
html,body{width:1200px;height:779px;overflow:hidden}
body{background:var(--stage);font-family:"Barlow Condensed",sans-serif;color:var(--white);position:relative}
.sheet{position:absolute;left:38px;top:31px;width:1124px;height:714px;overflow:hidden;background:var(--blue-mist);box-shadow:0 2px 6px rgba(0,0,0,.25)}
.abs{position:absolute}

/* showcase column */
.hero{left:0;top:0;width:551px;height:322px;background:var(--blue-deep)}
.hero__band{left:0;top:110px;width:551px;height:86px;background:var(--blue)}
.hero__art{left:44px;top:46px;width:170px;height:256px;border-radius:8px;background:linear-gradient(160deg,var(--gold) 0%,var(--teal-bright) 55%,var(--blue) 100%)}
.hero__mark{left:405px;top:22px;width:80px;height:62px;background:var(--gold)}
.hero__est{left:402px;top:96px;font-size:21px;font-weight:700}
.brand{left:200px;top:150px;width:340px;font-size:52px;line-height:.92;font-weight:800;text-transform:uppercase}
.model{left:0;top:293px;width:551px;text-align:center;font-size:16px}
.model em{color:var(--gold);font-weight:700}
.model .chev{color:var(--gold);font-weight:800;font-style:normal}
.showcase{left:0;top:322px;width:551px;height:224px;background:linear-gradient(180deg,var(--blue-mist) 0%,var(--blue-pale) 60%,var(--blue-mist) 61%,var(--blue-mist) 100%)}
.shirt{border-radius:18px 18px 6px 6px}
.shirt--olive{left:78px;top:342px;width:146px;height:164px;background:linear-gradient(180deg,#6e6a4a,#5a573c)}
.shirt--black{left:191px;top:352px;width:169px;height:170px;background:linear-gradient(180deg,#1a1a1a,#000)}
.shirt--royal{left:321px;top:342px;width:153px;height:166px;background:linear-gradient(180deg,#3a3fb0,#2a2f96)}
.warning{left:82px;top:546px;width:396px;height:46px;background:var(--blue-deep);clip-path:polygon(4% 0,96% 0,100% 100%,0 100%)}
.warning__text{left:0;top:548px;width:551px;text-align:center;font-size:15px;line-height:18px}
.warning__text em{color:var(--gold);font-weight:700}
.kit{left:0;top:589px;width:551px;height:125px;background:var(--blue-deep)}
.kit__title{left:28px;top:600px;font-size:38px;line-height:40px;font-weight:800;font-style:italic;text-transform:uppercase}
.kit__title span{display:block;color:var(--gold)}
.kit__item{top:599px;width:110px}
.kit__icon{width:48px;height:48px;border-radius:50%;background:var(--blue);border:2px solid var(--teal-soft);display:flex;align-items:center;justify-content:center;margin-left:16px}
.kit__label{margin-top:10px;font-size:16px;line-height:19px}
.kit__label em{color:var(--gold)}

/* ordering column */
.head__title{left:623px;top:14px;font-size:38px;font-weight:800;font-style:italic;text-transform:uppercase;letter-spacing:-.5px}
.head__title span{color:var(--gold)}
.head__sub{left:623px;top:56px;font-size:18px}
.tagline{left:992px;top:16px;width:120px;height:116px;background:var(--blue-mist);clip-path:polygon(6% 0,100% 0,94% 100%,0 100%)}
.tagline__text{left:1004px;top:28px;width:104px;font-size:21px;line-height:25px;font-weight:700;font-style:italic;color:var(--blue-deep)}
.step__icon{left:623px;width:89px;height:80px;background:var(--blue-deep);clip-path:polygon(0 0,100% 0,92% 100%,0 100%);display:flex;align-items:center;justify-content:center}
.step__num{left:721px;width:26px;height:24px;background:var(--teal);font-size:20px;font-weight:800;font-style:italic;text-align:center;line-height:24px}
.step__title{left:751px;font-size:16px;font-weight:800;font-style:italic;color:var(--blue-deep);text-transform:uppercase;border-bottom:1.5px solid var(--teal);padding-right:14px}
.step__body{left:748px;width:365px;font-size:15.5px;line-height:19.5px;color:var(--blue-deep)}
.info{left:582px;top:472px;width:542px;height:242px;background:var(--blue-deep)}
.about__title{left:623px;top:492px;font-size:27px;font-weight:800;font-style:italic;text-transform:uppercase;border-bottom:2px solid var(--gold);padding-right:30px}
.about__title span,.fine__title span{color:var(--gold)}
.about__body{left:623px;top:548px;width:290px;font-size:15.5px;line-height:19.5px}
.divider{left:918px;top:497px;width:1px;height:140px;background:var(--teal-soft)}
.fine__title{left:933px;top:503px;font-size:25px;font-weight:800;font-style:italic;text-transform:uppercase;border-bottom:2px solid var(--gold);padding-right:26px}
.fine__body{left:933px;top:536px;width:176px;font-size:11.5px;line-height:16px;font-style:italic;color:var(--blue-pale)}
.contact__rule{left:712px;top:660px;width:300px;height:1px;background:var(--blue-soft)}
.contact__icon{left:625px;top:668px;width:36px;height:36px;border:2px solid var(--white);border-radius:50%;display:flex;align-items:center;justify-content:center}
.contact__label{left:674px;top:668px;font-size:15px;line-height:19px;font-weight:800;font-style:italic;color:var(--gold);text-transform:uppercase}
.contact__body{left:748px;top:668px;width:366px;font-size:15.5px;line-height:19px}
.contact__body a{color:var(--gold);text-decoration:none}
</style>
</head>
<body>

<main class="sheet">
  <div class="abs hero"></div>
  <div class="abs hero__band"></div>
  <div class="abs hero__art" role="img" aria-label="Illustration of a sprinting figure in sneakers in front of a city skyline"></div>
  <div class="abs hero__mark"></div>
  <div class="abs hero__est">Est. 1979</div>
  <div class="abs brand">Copper Hollow Graphics</div>
  <div class="abs model"><span class="chev">«</span> <em>Model:</em> CHG Shop T-shirts <em>//</em> <em>Series:</em> Summer/Fall 2025 Collection <span class="chev">»</span></div>

  <div class="abs showcase"></div>
  <svg class="abs" style="left:0;top:322px" width="551" height="60" viewBox="0 0 551 60">
    <polygon points="0,0 105,0 0,40" fill="var(--blue-deep)"/>
    <polygon points="0,40 100,12 20,40" fill="var(--teal)"/>
  </svg>
  <div class="abs shirt shirt--olive" role="img" aria-label="Olive t-shirt printed with an equipment shop graphic and a vintage SUV"></div>
  <div class="abs shirt shirt--royal" role="img" aria-label="Royal blue t-shirt printed with a classic muscle car over a sunset graphic"></div>
  <div class="abs shirt shirt--black" role="img" aria-label="Black t-shirt printed with an off-road truck graphic"></div>

  <svg class="abs" style="left:420px;top:540px" width="131" height="60" viewBox="0 0 131 60">
    <polygon points="131,0 131,49 0,49" fill="var(--blue-deep)"/>
  </svg>
  <div class="abs warning"></div>
  <div class="abs warning__text"><em>⚠ WARNING:</em> These shirts may cause increased shop morale,<br>envy from competitors, and a high volume of customer demand.</div>

  <div class="abs kit"></div>
  <div class="abs kit__title">Merch Kit<span>Contents:</span></div>
  <div class="abs kit__item" style="left:228px">
    <div class="kit__icon"><svg width="26" height="26" viewBox="0 0 24 24" fill="#fff"><path d="M8 4l4 2 4-2 5 3-2 4-2-1v9H7v-9l-2 1-2-4z"/></svg></div>
    <div class="kit__label"><em>1.</em> Custom<br>&nbsp;&nbsp;Shop T-shirt</div>
  </div>
  <div class="abs kit__item" style="left:330px">
    <div class="kit__icon"><svg width="26" height="26" viewBox="0 0 24 24" fill="#fff"><path d="M8 4l4 2 4-2 5 3-2 4-2-1v10H7V10l-2 1-2-4z"/></svg></div>
    <div class="kit__label"><em>2.</em> Additional<br>&nbsp;&nbsp;Sample Shirt</div>
  </div>
  <div class="abs kit__item" style="left:431px">
    <div class="kit__icon"><svg width="26" height="26" viewBox="0 0 24 24"><path d="M5 4l14 14-1 2-2-1L3 6z" fill="#fff"/><path d="M18 18l2 3" stroke="#fff" stroke-width="1.5"/></svg></div>
    <div class="kit__label"><em>3.</em> CHG<br>&nbsp;&nbsp;Ink Pen</div>
  </div>

  <svg class="abs" style="left:582px;top:0" width="542" height="180" viewBox="0 0 542 180">
    <polygon points="0,0 542,0 542,116 405,116 395,132 380,116 110,116 0,160" fill="var(--blue-deep)"/>
    <polygon points="0,145 105,106 20,150 0,160" fill="var(--teal)"/>
  </svg>
  <div class="abs head__title">How to <span>Start an Order</span></div>
  <div class="abs head__sub">Choose you ride &gt; Pick your Gear &gt; We Customize</div>
  <div class="abs tagline"></div>
  <div class="abs tagline__text">Creating<br>T-shirts is<br>quick &amp; easy</div>

  <div class="abs step__icon" style="top:141px"><svg width="48" height="48" viewBox="0 0 48 48" fill="none" stroke="#fff" stroke-width="3"><circle cx="24" cy="24" r="21"/><path d="M14 26l3-8h14l3 8v6H14z"/><path d="M12 40l8-8"/></svg></div>
  <div class="abs step__num" style="top:142px">1.</div>
  <div class="abs step__title" style="top:144px">Choose your ride</div>
  <div class="abs step__body" style="top:168px">Send us a picture, or let us know the make and model of the vehicle you would like featured on your apparel.</div>

  <div class="abs step__icon" style="top:254px"><svg width="46" height="58" viewBox="0 0 46 58" fill="#fff"><path d="M14 2l9 4 9-4 12 7-5 9-4-2v22H11V16l-4 2-5-9z"/><rect x="18" y="28" width="8" height="26" rx="4" stroke="var(--blue-deep)" stroke-width="2"/></svg></div>
  <div class="abs step__num" style="top:255px">2.</div>
  <div class="abs step__title" style="top:257px">Pick your gear</div>
  <div class="abs step__body" style="top:281px">We will help you choose your t-shirts, sweatshirts or other apparel items and determine sizes and quantities.</div>

  <div class="abs step__icon" style="top:366px"><svg width="50" height="50" viewBox="0 0 50 50"><circle cx="25" cy="25" r="17" fill="none" stroke="#fff" stroke-width="8" stroke-dasharray="7 4"/><circle cx="25" cy="25" r="11" fill="#fff"/><rect x="21" y="20" width="8" height="24" fill="#fff"/><circle cx="25" cy="20" r="4" fill="var(--blue-deep)"/></svg></div>
  <div class="abs step__num" style="top:367px">3.</div>
  <div class="abs step__title" style="top:369px">We customize</div>
  <div class="abs step__body" style="top:393px">We make the magic happen and our team of expert artists will design your shirts and get a proof out to you. Upon order approval your order will go into production.</div>

  <div class="abs info"></div>
  <svg class="abs" style="left:582px;top:410px" width="542" height="64" viewBox="0 0 542 64">
    <polygon points="411,63 542,0 542,63" fill="var(--blue-deep)"/>
    <polygon points="461,40 542,10 542,18" fill="var(--teal)"/>
  </svg>
  <div class="abs about__title">About <span>Us:</span></div>
  <div class="abs about__body">Copper Hollow Graphics is a second-generation screen printing company in Ashford Mill, VA. For over 45 years, we’ve specialized in high-quality custom apparel and merchandise.</div>
  <div class="abs divider"></div>
  <div class="abs fine__title">The <span>Fine Print:</span></div>
  <div class="abs fine__body">Please send high-resolution photos of vehicles. When sending additional logos, please send vector images. Note that our shop minimum is 24 pieces for one-color prints and 100 pieces for full-color screen print. We also promise accurate, quality work.</div>
  <div class="abs contact__rule"></div>
  <div class="abs contact__icon"><svg width="20" height="14" viewBox="0 0 20 14" fill="none" stroke="#fff" stroke-width="2"><rect x="1" y="1" width="18" height="12" rx="2"/><path d="M1 2l9 6 9-6"/></svg></div>
  <div class="abs contact__label">Contact<br>CHG Sales:</div>
  <div class="abs contact__body">For more information, email us at <a>info@copperhollowtees.com</a>, or call <a>555-214-0387.</a> We look forward to working with you!</div>
</main>

</body>
</html>
```